Business Cards for a law firm

Business cards for our law firm. Use our silhoette logo and OAK PARTNERS - check our website (www.oakpartners.example)

Contact Information for Business Card

our silhouette logo, OAK PARTNERS, 800-555-0147, Dorian Pemberton, dorian@oakpartners.example

Requirements
Must have
• our silhouette logo, OAK PARTNERS, 800-555-0147, Dorian Pemberton, dorian@oakpartners.example

```html
<!DOCTYPE html>
<html lang="en">
<head>
<meta charset="utf-8">
<title>Oak Partners — Business Card</title>
<link href="https://fonts.googleapis.com/css2?family=Montserrat:wght@400&family=Source+Sans+3:wght@300;700&family=Roboto:wght@400&display=swap" rel="stylesheet">
<style>
  :root {
    --navy: #243468;
    --navy-deep: #1f2f64;
    --logo-blue: #3a6fc4;
    --paper: #ffffff;
    --backdrop: #dfe4e6;
    --ink-light: #ffffff;
  }
  * { box-sizing: border-box; margin: 0; padding: 0; }
  html, body {
    width: 1200px; height: 960px; overflow: hidden;
    background: var(--backdrop);
  }
  .canvas { position: relative; width: 1200px; height: 960px; }

  .card { position: absolute; overflow: hidden; }
  .card--front {
    left: 246px; top: 58px; width: 709px; height: 406px;
    background: var(--navy);
  }
  .card--back {
    left: 250px; top: 500px; width: 702px; height: 400px;
    background: var(--paper);
  }

  .brand-mark { position: absolute; }
  .brand-name {
    position: absolute;
    font-family: "Montserrat", sans-serif;
    font-weight: 400;
    line-height: 0.84;
    letter-spacing: 0.02em;
    transform: scaleX(1.25);
    transform-origin: left top;
  }

  .card--front .brand-mark {
    left: 140px; top: 150px; width: 80px; height: 80px;
    background: var(--logo-blue);
  }
  .card--front .brand-name {
    left: 237px; top: 146px;
    font-size: 58px;
    color: var(--logo-blue);
  }

  .card--back .brand-mark {
    left: 30px; top: 48px; width: 56px; height: 56px;
    background: var(--navy);
  }
  .card--back .brand-name {
    left: 109px; top: 40px;
    font-size: 38px;
    color: var(--navy);
  }

  .person-name {
    position: absolute; right: 31px; top: 33px;
    font-family: "Source Sans 3", sans-serif;
    font-size: 30px; letter-spacing: 0.03em;
    color: var(--navy); white-space: nowrap;
  }
  .person-name__first { font-weight: 700; }
  .person-name__last { font-weight: 300; }
  .name-tab {
    position: absolute; right: 0; top: 31px; width: 20px; height: 32px;
    background: var(--navy);
  }

  .contact-band {
    position: absolute; left: 0; bottom: 0; width: 100%; height: 115px;
    background: var(--navy-deep);
  }
  .contact-list { position: absolute; left: 30px; top: 20px; list-style: none; }
  .contact-item {
    display: flex; align-items: center; height: 22.5px;
    font-family: "Roboto", sans-serif; font-size: 19px; letter-spacing: 0.04em;
    color: var(--ink-light);
  }
  .contact-icon { width: 17px; height: 17px; margin-right: 10px; flex: none; }
</style>
</head>
<body>
<main class="canvas">
  <section class="card card--front" aria-label="Card front">
    <div class="brand-mark"></div>
    <div class="brand-name">OAK<br>PARTNERS</div>
  </section>

  <section class="card card--back" aria-label="Card back">
    <div class="brand-mark"></div>
    <div class="brand-name">OAK<br>PARTNERS</div>

    <h1 class="person-name"><span class="person-name__first">DORIAN</span> <span class="person-name__last">PEMBERTON</span></h1>
    <div class="name-tab"></div>

    <div class="contact-band">
      <ul class="contact-list">
        <li class="contact-item">
          <svg class="contact-icon" viewBox="0 0 24 24" fill="#fff" aria-hidden="true"><path d="M6.6 10.8a15 15 0 0 0 6.6 6.6l2.2-2.2c.3-.3.7-.4 1-.2 1.1.4 2.3.6 3.6.6.6 0 1 .4 1 1V20c0 .6-.4 1-1 1A17 17 0 0 1 3 4c0-.6.4-1 1-1h3.5c.6 0 1 .4 1 1 0 1.3.2 2.5.6 3.6.1.3 0 .7-.2 1z"/></svg>
          800-555-0147
        </li>
        <li class="contact-item">
          <svg class="contact-icon" viewBox="0 0 24 24" fill="none" stroke="#fff" stroke-width="2" aria-hidden="true"><circle cx="12" cy="12" r="10"/><path d="M2 12h20M12 2a15 15 0 0 1 0 20M12 2a15 15 0 0 0 0 20"/></svg>
          www.oakpartners.example
        </li>
        <li class="contact-item">
          <svg class="contact-icon" viewBox="0 0 24 24" fill="none" stroke="#fff" stroke-width="2" aria-hidden="true"><rect x="2" y="5" width="20" height="15"/><path d="M2 6l10 7 10-7"/></svg>
          dorian@oakpartners.example
        </li>
      </ul>
    </div>
  </section>
</main>
</body>
</html>
```